business card - Helicopter Flight Services, Flight School, etc.

We need a business card design for a new helicopter service.

We offer Helicopter Flight Services, Aerial Filming & Photography, Flight School, and Helicopter Tours. In that order.

Summit BladeAir, Inc.
Dennis Tollerby
SummitBladeair@Kestmail.com
626-418-7352

Based at the Brenwick Airport in Van Nuys, CA. The final design should communicate integrity and safety. Pictures or logos at your discretion.

Card back side - surprise me.

```html
<!DOCTYPE html>
<html lang="en">
<head>
<meta charset="utf-8">
<title>Summit BladeAir, Inc. — Business Card</title>
<link href="https://fonts.googleapis.com/css2?family=Open+Sans:wght@400;600;700&display=swap" rel="stylesheet">
<style>
  :root {
    --page: #ece9e4;
    --white: #ffffff;
    --blue: #1f6fbf;
    --blue-deep: #1556a8;
    --blue-light: #3a9fdc;
    --green: #8cc63f;
    --green-dark: #6fa82a;
    --shadow: rgba(0, 0, 0, 0.18);
  }
  * { box-sizing: border-box; margin: 0; padding: 0; }
  html, body {
    width: 1200px; height: 913px; overflow: hidden;
    background: var(--page);
    font-family: "Open Sans", Arial, sans-serif;
  }
  .canvas {
    position: relative; width: 1200px; height: 913px;
  }
  .card {
    position: absolute; width: 520px; height: 297px;
    left: 340px; overflow: hidden;
    box-shadow: 0 6px 18px var(--shadow);
  }
  .card--front { top: 118px; background: var(--white); }
  .card--back {
    top: 498px;
    background: linear-gradient(160deg, var(--blue-light) 0%, var(--blue) 55%, var(--blue-deep) 100%);
  }
  .card__shapes { position: absolute; inset: 0; }

  .brand {
    position: absolute; display: flex; align-items: center; gap: 10px;
  }
  .brand__dot {
    width: 22px; height: 22px; border-radius: 50%;
  }
  .brand__name {
    font-weight: 700; letter-spacing: 0.5px; white-space: nowrap;
  }
  .card--front .brand { left: 64px; top: 86px; }
  .card--front .brand__dot { background: var(--blue); }
  .card--front .brand__name { color: var(--blue); font-size: 26px; }
  .card--back .brand { left: 118px; top: 96px; }
  .card--back .brand__dot { background: var(--white); }
  .card--back .brand__name { color: var(--white); font-size: 28px; }

  .holder {
    position: absolute; right: 20px; top: 128px; text-align: right;
  }
  .holder__name { color: var(--white); font-weight: 700; font-size: 19px; line-height: 1.1; }
  .holder__role { color: var(--blue); font-size: 11px; font-weight: 400; }

  .contact {
    position: absolute; left: 22px; bottom: 22px; list-style: none;
    color: var(--white); font-size: 13px; line-height: 1.6;
  }
  .contact__item { display: flex; align-items: center; gap: 7px; }
  .contact__icon { width: 11px; height: 11px; flex: none; }

  .services {
    position: absolute; left: 40px; bottom: 30px; list-style: none;
    color: var(--white); font-size: 13.5px; line-height: 1.55;
  }
  .services__item { display: flex; align-items: center; gap: 8px; }
  .services__item::before {
    content: ""; width: 9px; height: 9px; border-radius: 50%;
    background: var(--green); flex: none;
  }
</style>
</head>
<body>
<main class="canvas">

  <section class="card card--front" aria-label="Card front">
    <svg class="card__shapes" viewBox="0 0 520 297" aria-hidden="true">
      <polygon points="0,176 288,176 300,164 520,164 520,170 303,170 291,182 0,182" fill="var(--green)"/>
      <polygon points="0,182 291,182 303,170 520,170 520,297 0,297" fill="var(--blue)"/>
      <polygon points="300,118 520,118 520,164 300,164 312,140" fill="var(--green)"/>
    </svg>

    <div class="brand">
      <span class="brand__dot"></span>
      <span class="brand__name">SUMMIT BLADEAIR, INC.</span>
    </div>

    <div class="holder">
      <p class="holder__name">Dennis Tollerby</p>
    </div>
    <p class="holder__role" style="position:absolute;right:20px;top:103px;">Owner</p>

    <ul class="contact">
      <li class="contact__item">
        <svg class="contact__icon" viewBox="0 0 12 12" aria-hidden="true"><path d="M2.5 1 L4.5 1 L5.2 3.4 L4 4.3 Q5 6.8 7.7 8 L8.6 6.8 L11 7.5 L11 9.5 Q10.5 11 9 11 Q1 10 1 3 Q1 1.5 2.5 1 Z" fill="var(--green)"/></svg>
        626-418-7352
      </li>
      <li class="contact__item">
        <svg class="contact__icon" viewBox="0 0 12 12" aria-hidden="true"><rect x="0.8" y="2.3" width="10.4" height="7.4" fill="none" stroke="var(--green)" stroke-width="1.2"/><path d="M1 2.6 L6 6.6 L11 2.6" fill="none" stroke="var(--green)" stroke-width="1.2"/></svg>
        SummitBladeair@Kestmail.com
      </li>
    </ul>
  </section>

  <section class="card card--back" aria-label="Card back">
    <div class="brand">
      <span class="brand__dot"></span>
      <span class="brand__name">SUMMIT BLADEAIR, INC.</span>
    </div>

    <ul class="services">
      <li class="services__item">Aerial Filming &amp; Photography</li>
      <li class="services__item">Flight School</li>
      <li class="services__item">Helicopter Tours (In that order)</li>
    </ul>
  </section>

</main>
</body>
</html>
```